Global (re)insurance broker needs a business card design

We need a classic business card for our company that is headquartered in SG, with offices in Malaysia and Dubai. We specialise in insurance and reinsurance broking and consultancy for our global clients.

```html
<!DOCTYPE html>
<html lang="en">
<head>
<meta charset="utf-8">
<title>Norvane – Business Card</title>
<link rel="stylesheet" href="https://fonts.googleapis.com/css2?family=Open+Sans:wght@400;600;700&display=swap">
<style>
  :root {
    --backdrop: #2c2c30;
    --card-dark: #1f1e23;
    --mark-faint: #2a292e;
    --sage: #c3deb7;
    --sage-deep: #a9cc9b;
    --sage-light: #d4e9ca;
    --royal: #2a4ea6;
    --ink-light: #e9e9ec;
    --white: #ffffff;
  }
  * { box-sizing: border-box; margin: 0; padding: 0; }
  html, body {
    width: 1200px;
    height: 780px;
    overflow: hidden;
    background: var(--backdrop);
    font-family: "Open Sans", Arial, sans-serif;
  }
  .canvas {
    position: relative;
    width: 1200px;
    height: 780px;
    display: flex;
    align-items: center;
    justify-content: center;
    gap: 40px;
  }
  .card {
    position: relative;
    width: 540px;
    height: 310px;
    border-radius: 4px;
    overflow: hidden;
    box-shadow: 0 14px 34px rgba(0, 0, 0, 0.45);
  }

  /* Front side */
  .card-front {
    background: var(--card-dark);
    color: var(--ink-light);
  }
  .front-mark-faint {
    position: absolute;
    right: 16px;
    bottom: 12px;
    font-size: 58px;
    font-weight: 600;
    letter-spacing: 2px;
    color: var(--mark-faint);
    line-height: 1;
    white-space: nowrap;
    z-index: 0;
  }
  .front-wordmark,
  .identity,
  .address,
  .contact-list {
    z-index: 1;
  }
  .front-wordmark {
    position: absolute;
    left: 150px;
    top: 22px;
    font-size: 54px;
    font-weight: 600;
    letter-spacing: 2px;
    color: var(--sage);
    line-height: 1;
  }
  .identity {
    position: absolute;
    left: 34px;
    top: 98px;
    padding-left: 14px;
    border-left: 6px solid var(--sage);
  }
  .person-name {
    font-size: 30px;
    font-weight: 700;
    line-height: 1.05;
  }
  .person-name .first { color: var(--royal); }
  .person-name .last { color: var(--sage); }
  .person-role {
    font-size: 14px;
    font-weight: 400;
    color: var(--ink-light);
    margin-top: 2px;
  }
  .address {
    position: absolute;
    left: 54px;
    top: 168px;
    font-size: 12.5px;
    line-height: 1.45;
    color: var(--ink-light);
  }
  .contact-list {
    position: absolute;
    left: 34px;
    top: 214px;
    list-style: none;
    font-size: 12.5px;
    line-height: 1.55;
  }
  .contact-list li {
    display: flex;
    align-items: center;
    gap: 8px;
  }
  .contact-list svg {
    width: 12px;
    height: 12px;
    flex: none;
  }

  /* Back side */
  .card-back {
    background: linear-gradient(100deg, var(--sage-deep) 0%, var(--sage) 45%, var(--sage-light) 100%);
  }
  .back-pattern {
    position: absolute;
    inset: 0;
  }
  .back-wordmark {
    position: absolute;
    left: 50%;
    bottom: 34px;
    transform: translateX(-50%);
    font-size: 20px;
    font-weight: 600;
    letter-spacing: 1px;
    color: var(--white);
  }
</style>
</head>
<body>
  <main class="canvas">
    <section class="card card-front" aria-label="Business card front">
      <div class="front-mark-faint" aria-hidden="true">NORVANE</div>

      <div class="front-wordmark">NORVANE</div>

      <div class="identity">
        <h1 class="person-name"><span class="first">Mira</span> <span class="last">Solen</span></h1>
        <p class="person-role">Chief Operating Officer</p>
      </div>

      <p class="address">48 Harbour Lane, Meridian<br>Tower #12-04, Singapore 068912</p>

      <ul class="contact-list">
        <li>
          <svg viewBox="0 0 12 12" aria-hidden="true"><rect x="3" y="0.8" width="6" height="10.4" rx="1" fill="none" stroke="var(--ink-light)" stroke-width="1"/><line x1="5" y1="9.5" x2="7" y2="9.5" stroke="var(--ink-light)" stroke-width="1"/></svg>
          <span>+65 9000 4821</span>
        </li>
        <li>
          <svg viewBox="0 0 12 12" aria-hidden="true"><circle cx="6" cy="6" r="5.2" fill="var(--royal)"/><path d="M1 6h10M6 0.8c2 2.8 2 7.6 0 10.4M6 0.8c-2 2.8-2 7.6 0 10.4" fill="none" stroke="var(--ink-light)" stroke-width="0.7"/></svg>
          <span>www.norvane.com</span>
        </li>
        <li>
          <svg viewBox="0 0 12 12" aria-hidden="true"><rect x="0.8" y="2.4" width="10.4" height="7.4" rx="0.8" fill="none" stroke="var(--ink-light)" stroke-width="1"/><path d="M1 3l5 3.8L11 3" fill="none" stroke="var(--ink-light)" stroke-width="1"/></svg>
          <span>mira@norvane.com</span>
        </li>
      </ul>
    </section>

    <section class="card card-back" aria-label="Business card back">
      <div class="back-pattern" role="img" aria-label="Repeating brand name pattern in soft sage green tones"></div>
      <div class="back-wordmark">NORVANE</div>
    </section>
  </main>
</body>
</html>
```